New travel store signage for Marlow Journeys to attract luxury travellers.

Hello,
We are looking to change the signage of our stores. The signage must include the following:
1. Marlow Journeys Logo (attached)
2. The text...The Travel & Cruise Experts
3. Brand Colours ( Fb0196, 412266, d41d84 and ffffff)
Please note the signage design must be central and only cover two thirds of the store front. We have also attached an image of one of our new stores which might be helpful when preparing a mock up.

We are looking for a quick turnaround on this, making a decision within 48 hours.

Target Market(s)

Retail

Industry/Entity Type

Travel Agency

Font styles to use
Other font styles liked:
• Radley

Colors
E54698
E96AAD
F1A4CE
F9D9EA
FCEFF6
6B429C
8869AF
B7A5CE
E3DAEB
F3F0F8

Requirements
Must have
• Hello, We are looking to change the signage of our stores. The signage must include the following: 1. Marlow Journeys Logo (attached) 2. The text...The Travel & Cruise Experts 3. Brand Colours ( Fb0196, 412266, d41d84 and ffffff) Please note the signage design must be central and only cover two thirds of the store front.
Should not have
• different colour or fonts. Gradient design.

```html
<!DOCTYPE html>
<html lang="en">
<head>
<meta charset="utf-8">
<title>Marlow Journeys – Store Signage</title>
<link href="https://fonts.googleapis.com/css2?family=EB+Garamond:wght@400;500&display=swap" rel="stylesheet">
<style>
  :root {
    --brand-pink: #d41d84;
    --brand-hot-pink: #fb0196;
    --brand-purple: #412266;
    --brand-white: #ffffff;
    --backdrop: #d9d9d9;
  }
  html, body {
    margin: 0;
    padding: 0;
    overflow: hidden;
  }
  .canvas {
    position: relative;
    width: 1200px;
    height: 919px;
    background: var(--backdrop);
    overflow: hidden;
  }
  .signboard {
    position: absolute;
    left: 40px;
    top: 389px;
    width: 1120px;
    height: 140px;
    display: flex;
    background: var(--brand-white);
  }
  .signboard__brand {
    flex: 0 0 410px;
    display: flex;
    align-items: center;
    justify-content: center;
    gap: 12px;
  }
  .brand-dot {
    width: 14px;
    height: 14px;
    border-radius: 50%;
    background: var(--brand-pink);
  }
  .brand-name {
    font-family: "EB Garamond", serif;
    font-weight: 500;
    font-size: 32px;
    color: var(--brand-purple);
    letter-spacing: 0.5px;
    white-space: nowrap;
  }
  .signboard__panel {
    flex: 1 1 auto;
    display: flex;
    align-items: center;
    justify-content: center;
    background: linear-gradient(90deg, var(--brand-pink) 0%, var(--brand-purple) 100%);
  }
  .signboard__tagline {
    margin: 0;
    font-family: "EB Garamond", serif;
    font-weight: 400;
    font-size: 52px;
    line-height: 1;
    color: var(--brand-white);
    letter-spacing: -0.5px;
    white-space: nowrap;
  }
</style>
</head>
<body>
  <main class="canvas">
    <section class="signboard" aria-label="Marlow Journeys shop fascia sign">
      <div class="signboard__brand">
        <span class="brand-dot"></span>
        <span class="brand-name">Marlow Journeys</span>
      </div>
      <div class="signboard__panel">
        <h1 class="signboard__tagline">The Travel &amp; Cruise Experts</h1>
      </div>
    </section>
  </main>
</body>
</html>
```